Website Design Required For Education Video Portfolio Site

I am looking for a designer to create a skin for a relaunch of my website - www.brackenlearningfilms.co.uk. We want a clean and stylish new design.

The website showcases prospectus/promotional videos that are made for schools and colleges. Videos will be hosted on video channel and embedded.

I want it to be stylish and clean.

I require 7 pages designed and this must be agreed in order to do the project.

1. Homepage
2. About
3. Prices
4. Testimonials
5. Contact Page with form
6. Promotional Videos
7. Subject Videos

The website will be then be built on the Wordpress system.

Target Market(s)

Education, Schools, Colleges, Universities

Industry/Entity Type

Education

Font styles to use
Serif

Colors

Designer to choose colors to be used in the design.

Requirements
Must have
• Video content, be clean, show our portfolio, descriptions about videos. I like the idea of having video headers.
Nice to have
• Images

```html
<!DOCTYPE html>
<html lang="en">
<head>
<meta charset="utf-8">
<title>Bracken Learning Films – Home</title>
<link rel="stylesheet" href="https://fonts.googleapis.com/css2?family=Raleway:wght@400;500;600;700&family=Roboto+Slab:wght@400;500;700&display=swap">
<style>
:root{
  --blue:#1aa7ec;
  --blue-deep:#0b8fd1;
  --sky:#e4f3fb;
  --ink:#2b2b2b;
  --text:#4a4a4a;
  --white:#ffffff;
  --footer:#2f3033;
  --rule:#d9d9d9;
}
*{box-sizing:border-box;margin:0;padding:0}
html,body{width:1200px;height:4136px;overflow:hidden}
body{position:relative;font-family:'Raleway',sans-serif;color:var(--text);background:var(--white)}
h1,h2,h3{font-weight:400}
.abs{position:absolute}
a{color:inherit;text-decoration:none}

/* Hero */
.hero{left:0;top:0;width:1200px;height:643px;background:linear-gradient(160deg,#5c6258 0%,#3f4640 40%,#6d7065 70%,#2f3530 100%)}
.hero-shade{left:0;top:0;width:1200px;height:643px;background:rgba(0,0,0,.25)}
.brand{left:112px;top:16px;display:flex;align-items:center;gap:8px;color:var(--blue);font-weight:700;font-size:24px}
.brand-dot{width:22px;height:22px;border-radius:50%;background:var(--blue)}
.channel{left:871px;top:27px;width:22px;height:22px;border-radius:50%;background:var(--white)}
.btn{display:flex;align-items:center;justify-content:center;gap:12px;border-radius:24px;font-weight:700;font-size:14px;letter-spacing:.3px}
.btn-contact{left:933px;top:16px;width:153px;height:43px;background:var(--blue);color:var(--white)}
.arrow{width:20px;height:20px}
.nav-rule{left:393px;top:79px;width:693px;height:1px;background:rgba(255,255,255,.6)}
.nav{top:96px;font-size:13px;font-weight:500;color:var(--white);letter-spacing:.2px}
.nav.active{color:var(--blue)}
.hero-kicker{left:0;width:1200px;top:275px;text-align:center;color:var(--white);font-size:23px;font-weight:400}
.hero-title{left:0;width:1200px;top:315px;text-align:center;color:var(--white);font-size:50px;font-weight:700}
.play{display:flex;align-items:center;gap:8px;color:var(--white);font-size:12px;text-decoration:underline}
.play-hero{left:553px;top:386px}
.dots{left:560px;top:606px;display:flex;gap:9px}
.dots span{width:12px;height:12px;border-radius:50%;background:rgba(255,255,255,.75)}
.dots span.on{background:var(--blue)}

/* Feature video */
.video-card{left:254px;top:727px;width:677px;height:426px;border:8px solid var(--blue);border-radius:10px;box-shadow:0 6px 14px rgba(0,0,0,.18);background:linear-gradient(120deg,#7b4a3a,#a4624a 40%,#4f6b55 75%,#3b5d47)}
.play-card{left:275px;top:194px;font-size:17px}
.video-title{left:24px;top:316px;font-family:'Roboto Slab',serif;color:#f2efe6;font-size:27px;font-weight:700;line-height:1}
.video-sub{left:24px;top:344px;font-family:'Roboto Slab',serif;color:#f2efe6;font-size:27px;font-weight:400;line-height:1;letter-spacing:.5px}

/* Intro */
.intro-head{left:111px;top:1197px;width:460px;font-size:27px;line-height:43px;color:var(--ink)}
.intro-body{left:597px;top:1195px;width:473px;font-size:15px;line-height:25px;text-align:justify}
.intro-body p+p{margin-top:15px}

/* Investment band */
.band-photo{left:0;top:1466px;width:569px;height:577px;background:linear-gradient(170deg,#8a8d86,#5f7a61 55%,#2e6b42)}
.band{left:569px;top:1466px;width:631px;height:577px;background:var(--blue-deep)}
.band-head{left:604px;top:1545px;width:460px;font-size:27px;line-height:43px;color:var(--white)}
.band-body{left:604px;top:1643px;width:473px;font-size:15px;line-height:25px;color:var(--white);text-align:justify}
.band-body p+p{margin-top:15px}
.btn-feedback{left:604px;top:1911px;width:241px;height:46px;background:var(--white);color:var(--blue-deep)}

/* Values */
.values{left:0;top:2043px;width:1200px;height:446px;background:var(--sky)}
.value-card{top:2130px;width:310px;height:269px;background:var(--white);border-radius:6px;box-shadow:0 4px 10px rgba(0,0,0,.12);text-align:center;padding-top:30px}
.value-card svg{width:70px;height:70px}
.value-card p{margin:20px auto 0;width:270px;font-size:14px;line-height:26px}

/* Custom */
.custom-head{left:111px;top:2564px;width:420px;font-size:27px;line-height:43px;color:var(--ink)}
.custom-body{left:111px;top:2710px;width:473px;font-size:15px;line-height:25px;text-align:justify}
.custom-body p+p{margin-top:15px}
.link-box{left:93px;top:2902px;width:553px;height:74px;background:var(--sky);padding:10px 18px}
.link-box span{display:block;font-size:14px;color:var(--ink)}
.link-box a{display:block;font-size:19px;color:var(--ink);text-decoration:underline;margin-top:4px}
.btn-watch{left:111px;top:3000px;width:236px;height:46px;background:var(--blue);color:var(--white)}
.custom-photo{left:646px;top:2489px;width:554px;height:576px;background:linear-gradient(150deg,#cfc7b7,#9fa79a 40%,#3b7a55 70%,#c2b7a6)}

/* Partners */
.partners-head{left:0;width:1200px;top:3173px;text-align:center;font-size:27px;color:var(--ink)}
.partners-rule{left:112px;width:975px;top:3397px;height:1px;background:var(--rule)}
.partners-div{width:1px;background:var(--rule)}
.badge{background:#d6dde3}

/* Footer */
.footer{left:0;top:3679px;width:1200px;height:457px;background:var(--footer)}
.foot-brand{left:0;width:1200px;top:3740px;display:flex;justify-content:center;align-items:center;gap:12px;color:var(--blue);font-size:38px;font-weight:700}
.foot-brand .brand-dot{width:40px;height:40px}
.foot-rule{left:112px;width:975px;height:1px;background:#55575b}
.foot-col{top:3870px;width:330px;color:#e6e6e6}
.foot-col h3{font-size:23px;color:var(--white);padding-bottom:10px;border-bottom:1px solid #6b6d70;width:190px}
.foot-col p{margin-top:16px;font-size:15px;line-height:25px}
.legal{top:4078px;font-size:14px;color:#e6e6e6}
</style>
</head>
<body>

<!-- Hero -->
<div class="abs hero" role="img" aria-label="Aerial video still of a school campus and its surrounding streets"></div>
<div class="abs hero-shade"></div>
<div class="abs brand"><span class="brand-dot"></span>Bracken Learning Films</div>
<a class="abs channel" href="#" aria-label="Video channel"></a>
<a class="abs btn btn-contact" href="#">CONTACT
  <svg class="arrow" viewBox="0 0 20 20"><circle cx="10" cy="10" r="10" fill="#fff"/><path d="M8 6l4 4-4 4" fill="none" stroke="#1aa7ec" stroke-width="2"/></svg>
</a>
<div class="abs nav-rule"></div>
<a class="abs nav active" style="left:393px" href="#">HOME</a>
<a class="abs nav" style="left:475px" href="#">ABOUT</a>
<a class="abs nav" style="left:560px" href="#">PROMOTIONAL VIDEOS</a>
<a class="abs nav" style="left:753px" href="#">SUBJECT VIDEOS</a>
<a class="abs nav" style="left:904px" href="#">PRICES</a>
<a class="abs nav" style="left:989px" href="#">TESTIMONIALS</a>
<div class="abs hero-kicker">WE MAKE AWESOME EDUCATIONAL</div>
<div class="abs hero-title">Videos</div>
<a class="abs play play-hero" href="#">
  <svg width="30" height="30" viewBox="0 0 30 30"><circle cx="15" cy="15" r="15" fill="#fff"/><path d="M12 9l9 6-9 6z" fill="#1aa7ec"/></svg>Play Video
</a>
<div class="abs dots"><span></span><span class="on"></span><span></span><span></span></div>

<!-- Feature video -->
<div class="abs video-card" role="img" aria-label="Video thumbnail of young children playing with water at nursery">
  <a class="abs play play-card" href="#">
    <svg width="40" height="40" viewBox="0 0 30 30"><circle cx="15" cy="15" r="15" fill="#fff"/><path d="M12 9l9 6-9 6z" fill="#1aa7ec"/></svg>Play Video
  </a>
  <div class="abs video-title">EARLY YEARS VIDEOS</div>
  <div class="abs video-sub">The gateway to your school</div>
</div>

<!-- Intro -->
<h1 class="abs intro-head">CREATING BESPOKE EDUCATION VIDEOS TO SHOWCASE SCHOOLS, COLLEGES &amp; TRAINING PROVIDERS IN THE NORTH OF ENGLAND</h1>
<div class="abs intro-body">
  <p>Here at Bracken Learning Films, we know how to create stylish, engaging, and successful educational videos for schools, colleges and training providers. We’ve been making them for years.</p>
  <p>We believe that when you’re trying to attract new learners the best way to show how your learning establishment is better than the rest is with a compelling, top-quality video.</p>
</div>

<!-- Investment band -->
<div class="abs band-photo" role="img" aria-label="Photo of a pupil in green uniform on playground climbing bars"></div>
<div class="abs band"></div>
<h2 class="abs band-head">A ONE-OFF INVESTMENT THAT BRINGS LONG-TERM RESULTS</h2>
<div class="abs band-body">
  <p>There are so many ways to repurpose your videos and make the initial investment work for you – sharing snippets on social media, embedding the video onto your website, uploading it to your online video channel or playing it on your welcome screen in reception. The return on investment is excellent (and in some cases, instant!)</p>
  <p>BY THE WAY: don’t just take our word for how successful our videos are. Check out some of the wonderful feedback we’ve received.</p>
</div>
<a class="abs btn btn-feedback" href="#">READ OUR FEEDBACK
  <svg class="arrow" viewBox="0 0 20 20"><circle cx="10" cy="10" r="10" fill="#0b8fd1"/><path d="M8 6l4 4-4 4" fill="none" stroke="#fff" stroke-width="2"/></svg>
</a>

<!-- Values -->
<div class="abs values"></div>
<div class="abs value-card" style="left:112px">
  <svg viewBox="0 0 70 70" fill="none" stroke="#222" stroke-width="2.5"><rect x="12" y="28" width="46" height="32" rx="3"/><path d="M12 20l44-8 2 10-44 8z"/><path d="M22 18l6 8M34 16l6 8M46 14l6 8M12 36h46"/><path d="M31 42v12l10-6z" stroke="#1aa7ec"/></svg>
  <p>We’re a smart bunch of experienced video makers and we know how to create compelling videos that get results.</p>
</div>
<div class="abs value-card" style="left:445px">
  <svg viewBox="0 0 70 70" fill="none" stroke="#222" stroke-width="2.5"><path d="M14 40l26-26 16 16-26 26z"/><path d="M14 40l-4 6 14 14 6-4"/><path d="M22 52l-6 12"/><path d="M50 10l4-8M58 18l8-4M54 14l6-6" stroke="#1aa7ec"/></svg>
  <p>We offer a cost-effective marketing solution – no more expensive brochure designing, printing and storage hassles. A video beats traditional marketing materials hands down.</p>
</div>
<div class="abs value-card" style="left:777px">
  <svg viewBox="0 0 70 70" fill="none" stroke="#222" stroke-width="2.5"><path d="M20 20A26 26 0 1 1 12 38"/><path d="M20 10v10H10"/><path d="M35 22v14l8 6" stroke="#1aa7ec"/></svg>
  <p>We save you time and effort – you could invest time, effort and tech into making your own videos, but would they have the same polished, professional impact as ours?</p>
</div>

<!-- Custom -->
<h2 class="abs custom-head">CREATING CUSTOMISED EDUCATIONAL VIDEOS THAT EXCEED YOUR EXPECTATIONS</h2>
<div class="abs custom-body">
  <p>Prefer a prospectus video over a music-driven one? No problem. In fact, we can almost always cater for your specific needs and budgets. All you have to do is ask.</p>
  <p>Our mission is to capture the heart and soul of your school, college, training company, so your potential recruits can’t resist taking that next step towards enrolling.</p>
</div>
<div class="abs link-box">
  <span>Take a look at our range of video offerings</span>
  <a href="#">https://brackenlearningfilms.co.uk/our-work/.</a>
</div>
<a class="abs btn btn-watch" href="#">WATCH OUR VIDEOS
  <svg class="arrow" viewBox="0 0 20 20"><circle cx="10" cy="10" r="10" fill="#fff"/><path d="M8 6l4 4-4 4" fill="none" stroke="#1aa7ec" stroke-width="2"/></svg>
</a>
<div class="abs custom-photo" role="img" aria-label="Photo of two young pupils holding colourful ribbons"></div>

<!-- Partners -->
<h2 class="abs partners-head">SCHOOLS, COLLEGES AND TRAINING PROVIDERS WE'VE WORKED WITH</h2>
<div class="abs partners-rule"></div>
<div class="abs partners-div" style="left:274px;top:3244px;height:153px"></div>
<div class="abs partners-div" style="left:481px;top:3244px;height:153px"></div>
<div class="abs partners-div" style="left:690px;top:3244px;height:153px"></div>
<div class="abs partners-div" style="left:899px;top:3244px;height:153px"></div>
<div class="abs partners-div" style="left:274px;top:3421px;height:169px"></div>
<div class="abs partners-div" style="left:481px;top:3421px;height:169px"></div>
<div class="abs partners-div" style="left:690px;top:3421px;height:169px"></div>
<div class="abs partners-div" style="left:899px;top:3421px;height:169px"></div>

<div class="abs badge" role="img" aria-label="Partner college badge" style="left:120px;top:3265px;width:112px;height:96px;border-radius:8px"></div>
<div class="abs badge" role="img" aria-label="Partner nursery badge" style="left:330px;top:3260px;width:118px;height:104px;border-radius:8px"></div>
<div class="abs badge" role="img" aria-label="Partner language club badge" style="left:538px;top:3292px;width:108px;height:40px;border-radius:6px"></div>
<div class="abs badge" role="img" aria-label="Partner primary school badge" style="left:752px;top:3261px;width:92px;height:92px;border-radius:50%"></div>
<div class="abs badge" role="img" aria-label="Partner tech club badge" style="left:950px;top:3289px;width:108px;height:48px;border-radius:4px"></div>
<div class="abs badge" role="img" aria-label="Partner school badge" style="left:150px;top:3437px;width:86px;height:96px;border-radius:8px"></div>
<div class="abs badge" role="img" aria-label="Partner school badge" style="left:342px;top:3427px;width:100px;height:100px;border-radius:50%"></div>
<div class="abs badge" role="img" aria-label="Partner primary school badge" style="left:538px;top:3427px;width:104px;height:104px;border-radius:50%"></div>
<div class="abs badge" role="img" aria-label="Partner primary school badge" style="left:740px;top:3427px;width:106px;height:106px;border-radius:50%"></div>
<div class="abs badge" role="img" aria-label="Partner primary school badge" style="left:940px;top:3427px;width:106px;height:106px;border-radius:50%"></div>

<!-- Footer -->
<footer class="abs footer"></footer>
<div class="abs foot-brand"><span class="brand-dot"></span>Bracken Learning Films</div>
<div class="abs foot-rule" style="top:3840px"></div>
<div class="abs foot-col" style="left:117px"><h3>OUR MISSION</h3><p>Striving to deliver quality video<br>content for schools and colleges<br>in the North of England.</p></div>
<div class="abs foot-col" style="left:477px"><h3>CONTACT US</h3><p>01632 960 418<br>hello@brackenlearningfilms.co.uk</p></div>
<div class="abs foot-col" style="left:830px"><h3>VISIT</h3><p>Studio 4, Fellgate Business Park,<br>Consett, Durham. DH8 0XZ.</p></div>
<div class="abs foot-rule" style="top:4036px"></div>
<div class="abs legal" style="left:112px">© Bracken Learning Films Limited 2023. All Rights Reserved.</div>
<div class="abs legal" style="left:772px">Company Registration Number: 10458721.</div>

</body>
</html>
```